Captivating packaging design for sports company.

We need a packaging design that encompasses our resistance bands workout set. Our focus is quality, convenience, and versatility. The design should be tailored to our broad array of customer across all paths. We would like the packaging to reflect our brand and product features such as: the LBS(weight) listed on each of the bands, convenience for travel and at home, highest quality, for all fitness levels, and free eBook. We'd also like to include a couple of our reviews on the packaging. Please refer to our listing on Varlo for additional information https://www.shopvarlo.com/Brisklane-Athletics-Resistance-Workout-Carrying/dp/K47TR2XMNQ/ref=sr_1_1?ie=UTF8&qid=1470453588&sr=8-1&keywords=brisklane+athletics+resistance+bands
Please reach out with additional questions for any further details. Thank you.
Target Market(s)
Sports, fitness, and health enthusiasts of all ages.
Industry/Entity Type
It Company
Look and feel
Each slider illustrates characteristics of the customer's brand and the style your logo design should communicate.

```html
<!DOCTYPE html>
<html lang="en">
<head>
<meta charset="utf-8">
<title>Brisklane Athletics Resistance Band Packaging</title>
<link rel="stylesheet" href="https://fonts.googleapis.com/css2?family=Michroma&family=Roboto:wght@500;700&display=swap">
<style>
  :root {
    --navy: #1c2a4f;
    --sky: #9fd5f3;
    --sky-deep: #1f86c5;
    --ink: #1a1a1a;
    --white: #ffffff;
    --backdrop: #d6d6d6;
    --photo-dark: #22303d;
    --photo-mid: #6f9cb8;
  }
  * { box-sizing: border-box; margin: 0; padding: 0; }
  html, body { width: 1200px; height: 1199px; overflow: hidden; }
  body {
    background: var(--backdrop);
    font-family: "Michroma", sans-serif;
    position: relative;
  }
  .package { position: absolute; left: 150px; top: 235px; width: 900px; height: 730px; display: flex; }

  /* side panel */
  .side-panel {
    width: 250px; height: 100%; background: var(--navy); color: var(--white);
    position: relative; padding: 70px 22px 0;
  }
  .brand-mark { display: flex; align-items: center; gap: 10px; }
  .brand-mark .dot { width: 22px; height: 22px; border-radius: 50%; background: currentColor; flex: none; }
  .brand-mark .name { font-size: 15px; line-height: 1.2; }
  .contents { margin-top: 150px; font-size: 11px; line-height: 1.6; text-align: center; letter-spacing: .5px; }
  .contents h3 { font-size: 11px; font-weight: 400; }
  .slogan { position: absolute; left: 22px; right: 22px; top: 450px; font-size: 38px; line-height: 1.2; text-align: center; }
  .total-box {
    position: absolute; left: 22px; right: 22px; bottom: 30px; height: 100px;
    background: var(--sky); color: var(--navy); font-size: 13px; line-height: 1.35;
    display: flex; align-items: center; justify-content: center; text-align: center;
  }

  /* front panel */
  .front-panel { flex: 1; height: 100%; background: var(--sky); position: relative; overflow: hidden; }
  .athlete-photo {
    position: absolute; left: 0; top: 20px; width: 330px; height: 710px;
    background: radial-gradient(ellipse at 45% 40%, var(--photo-mid), var(--photo-dark) 60%, transparent 80%);
  }
  .front-brand { position: absolute; left: 330px; right: 0; top: 60px; color: var(--ink); display: flex; flex-direction: column; align-items: center; gap: 12px; }
  .front-brand .dot { width: 48px; height: 48px; border-radius: 50%; background: var(--ink); }
  .front-brand .name { font-size: 22px; text-align: center; line-height: 1.2; }
  .title-banner {
    position: absolute; left: 280px; right: 0; top: 215px; height: 150px;
    background: var(--navy); color: var(--white); padding: 30px 0 0 22px;
    border-bottom: 6px solid var(--sky-deep);
  }
  .title-banner .kicker { font-size: 15px; }
  .title-banner .headline { font-size: 32px; line-height: 1.2; margin-top: 6px; white-space: nowrap; }
  .set-name { position: absolute; left: 320px; top: 395px; font-size: 21px; line-height: 1.3; color: var(--sky-deep); }
  .features { position: absolute; left: 320px; top: 500px; list-style: none; font-size: 13px; line-height: 1.4; color: var(--navy); }
  .use-badge {
    position: absolute; right: 45px; top: 560px; width: 110px; height: 110px; border-radius: 50%;
    border: 2px solid var(--navy); color: var(--navy); font-family: "Roboto", sans-serif; font-weight: 700;
    font-size: 8px; display: flex; flex-direction: column; align-items: center; justify-content: center; gap: 6px; text-align: center; padding: 0 10px;
  }
  .use-badge .dot { width: 26px; height: 26px; border-radius: 50%; background: var(--sky-deep); }
  .bonus-badge { position: absolute; left: 115px; top: 525px; width: 180px; height: 180px; }
  .bonus-badge svg { display: block; }
  .bonus-badge .text {
    position: absolute; inset: 0; display: flex; flex-direction: column; align-items: center; justify-content: center;
    color: var(--white); text-align: center; font-size: 10px; line-height: 1.35;
  }
  .bonus-badge .text strong { font-size: 22px; font-weight: 400; }
</style>
</head>
<body>
  <div class="package">
    <section class="side-panel">
      <div class="brand-mark"><span class="dot"></span><span class="name">BRISKLANE<br>ATHLETICS</span></div>
      <div class="contents">
        <h3>IN THE BOX</h3>
        <p>x1 YELLOW - 2-4LB<br>x1 GREEN - 4-6LB<br>x1 BLUE - 10-12LB<br>x1 RED - 15-20LB<br>x1 BLACK - 25-30LB<br>CARRY CASE<br>E-BOOK</p>
      </div>
      <div class="slogan">TONE<br>BURN<br>BUILD</div>
      <div class="total-box">UP TO 75LBS<br>OF TOTAL<br>RESISTANCE</div>
    </section>

    <section class="front-panel">
      <div class="athlete-photo" role="img" aria-label="Photo of an athlete in a cap and sports top exercising with a resistance band"></div>
      <div class="front-brand"><span class="dot"></span><span class="name">BRISKLANE<br>ATHLETICS</span></div>
      <div class="title-banner">
        <div class="kicker">HIGH QUALITY</div>
        <div class="headline">RESISTANCE<br>BANDS</div>
      </div>
      <div class="set-name">Brisklane Athletics<br>Resistance Band<br>Workout Set</div>
      <ul class="features">
        <li>4 Colourful Bands</li>
        <li>Door Anchor</li>
        <li>2 Handles</li>
        <li>2 Ankle Straps</li>
        <li>Carrying Case</li>
      </ul>
      <div class="use-badge"><span>GREAT FOR INDOORS OR OUTDOORS</span><span class="dot"></span><span>ANYTIME ANYWHERE</span></div>
      <div class="bonus-badge">
        <svg width="180" height="180" viewBox="0 0 180 180" aria-hidden="true">
          <polygon fill="#1c2a4f" points="90,5 112,30 145,22 150,55 176,75 158,102 170,135 136,140 120,170 90,155 60,170 44,140 10,135 22,102 4,75 30,55 35,22 68,30"/>
        </svg>
        <div class="text"><strong>BONUS</strong>Product and<br>Workout<br>Guide eBook</div>
      </div>
    </section>
  </div>
</body>
</html>
```